Freight broker online presence/customer portal track shipping

I sleek design showing what we do, broker freight. What we specialize in, chemicals and any freight where domestic or international. We want a home page, a customer portal button on front page that lets clients check on status of their freight (integrate with our transportation management system. Contact page,
COMPANIES THAT HAVE PALLETS TO MOVE.
https://www.tallowmerelogistics.com/
https://www.quivendale.com/
https://www.rkpellow.com/
3 page

```html
<!DOCTYPE html>
<html lang="en">
<head>
<meta charset="utf-8">
<title>Corvane Freight — Freight Broker</title>
<link rel="stylesheet" href="https://fonts.googleapis.com/css2?family=Dela+Gothic+One&family=Roboto:wght@400;500;700&display=swap">
<style>
:root{
  --blue:#2f6db5;
  --blue-dark:#25589a;
  --teal:#2bb5a0;
  --red:#e8363b;
  --ink:#1b1b1b;
  --text:#6b6b6b;
  --grey-bg:#f3f3f3;
  --footer:#3b3b3b;
  --white:#ffffff;
}
*{box-sizing:border-box;margin:0;padding:0}
html,body{width:1200px;height:3773px;overflow:hidden;background:var(--white)}
body{font-family:"Roboto",Arial,sans-serif;color:var(--ink)}
.page{position:relative;width:1200px;height:3773px;overflow:hidden}
.abs{position:absolute}
.display{font-family:"Dela Gothic One","Arial Black",sans-serif;font-weight:400;letter-spacing:.5px;text-transform:uppercase}
.section-title{position:absolute;left:0;width:1200px;text-align:center;font-size:31px;color:var(--ink)}
.pill{position:absolute;display:flex;align-items:center;justify-content:center;gap:10px;border-radius:26px;color:var(--white);font-weight:700;font-size:14px;text-transform:uppercase}
.pill svg{width:14px;height:14px}
.pill.teal{background:var(--teal)}
.pill.blue{background:var(--blue)}

/* hero */
.hero-photo{position:absolute;left:0;top:0;width:1200px;height:800px;
  background:radial-gradient(ellipse at 62% 30%,#e9a06a 0%,#b8623e 22%,transparent 50%),
  linear-gradient(180deg,#1e2c48 0%,#3b3d55 35%,#6a4a42 60%,#2a3850 100%)}
.hero-truck{position:absolute;left:640px;top:180px;width:520px;height:500px;border-radius:40px;
  background:radial-gradient(ellipse at 55% 45%,#d8353a 0%,#a92127 45%,transparent 72%)}
.nav-logo{left:105px;top:24px;display:flex;align-items:center;gap:10px;color:var(--white);font-weight:700;font-size:17px}
.nav-logo i{display:block;width:40px;height:40px;border-radius:50%;background:var(--blue)}
.nav{left:303px;top:39px;display:flex;gap:26px;font-size:13.5px;font-weight:700;color:var(--white);text-transform:uppercase}
.nav .active{color:#5c9be0}
.portal{left:897px;top:26px;width:197px;height:47px;background:var(--red)}
.hero-title{left:111px;top:220px;font-size:41px;color:var(--white)}
.hero-text{left:112px;top:288px;width:470px;font-size:16px;line-height:26px;color:var(--white)}
.hero-btn{left:113px;top:365px;width:198px;height:48px}

/* services */
.svc{position:absolute;top:861px;width:313px;height:317px;background:var(--blue);border-radius:8px;border:2px solid #3f7dc4}
.svc .ph{position:absolute;left:0;top:0;right:0;height:223px;border-radius:6px 6px 0 0}
.svc .ph::after{content:"";position:absolute;left:0;right:0;bottom:0;height:28px;background:linear-gradient(172deg,transparent 50%,var(--teal) 51%)}
.svc h3{position:absolute;top:240px;left:0;right:0;text-align:center;color:var(--white);font-size:15.5px;line-height:21px;font-weight:700;text-transform:uppercase}
.circle-arrow{position:absolute;width:40px;height:40px;border-radius:50%;background:var(--white);box-shadow:0 2px 6px rgba(0,0,0,.25);display:flex;align-items:center;justify-content:center}
.svc .circle-arrow{left:50%;bottom:-20px;margin-left:-20px}
.circle-arrow svg{width:20px;height:14px}

/* broker */
.broker{position:absolute;left:21px;top:1428px;width:1157px;height:466px;border-radius:16px;overflow:hidden;
  background:linear-gradient(90deg,#6b4636 0%,#b57a52 25%,#8b8f96 45%,#c8c3bd 60%);box-shadow:0 4px 14px rgba(0,0,0,.12)}
.broker-copy{position:absolute;left:518px;top:0;width:700px;height:466px;border-top-left-radius:120px 466px;
  background:linear-gradient(100deg,#ffffff 0%,#f2f2f2 60%,#e6e6e6 100%)}
.broker-copy h2{position:absolute;left:72px;top:72px;font-size:34px}
.broker-copy p{position:absolute;left:72px;top:125px;width:480px;font-size:16px;line-height:26.5px;color:var(--text)}
.broker-copy .pill{left:73px;top:362px;width:163px;height:48px}

/* specialized */
.spec{position:absolute;top:2093px;width:448px;height:393px}
.spec .frame{position:absolute;inset:0}
.spec .ph{position:absolute;width:446px;height:393px;top:9px}
.spec .label{position:absolute;left:46px;bottom:40px;color:var(--white);font-size:28px}
.spec .circle-arrow{right:44px;bottom:32px;width:38px;height:38px}

/* blog */
.blog-bg{position:absolute;left:0;top:2608px;width:1200px;height:600px;background:var(--grey-bg)}
.post{position:absolute;top:2764px;width:315px;height:378px;background:var(--white);border-radius:6px;overflow:hidden;box-shadow:0 2px 8px rgba(0,0,0,.06)}
.post .ph{position:absolute;left:0;top:0;width:315px;height:206px}
.post .date{position:absolute;left:0;top:138px;width:61px;height:68px;background:var(--teal);color:var(--white);text-align:center;padding-top:8px}
.post .date b{display:block;font-family:"Dela Gothic One",sans-serif;font-weight:400;font-size:24px;line-height:26px}
.post .date span{display:block;font-family:"Dela Gothic One",sans-serif;font-size:14px;line-height:18px}
.post h4{position:absolute;left:21px;top:232px;font-size:13.5px;font-weight:700;text-transform:uppercase}
.post hr{position:absolute;left:21px;top:257px;width:30px;border:0;border-top:3px solid var(--teal)}
.post p{position:absolute;left:21px;top:276px;width:275px;font-size:14px;line-height:22px;color:var(--text)}
.post .pill{left:22px;top:327px;width:113px;height:34px;font-size:12px}

/* footer */
.footer-bg{position:absolute;left:0;top:3150px;width:1200px;height:623px}
.fcol{position:absolute;top:3449px}
.fcol h5{font-size:14px;font-weight:700;color:var(--white);text-transform:uppercase}
.fcol h5::after{content:"";display:block;width:48px;height:2px;background:var(--white);margin-top:6px}
.fcol ul{list-style:none;margin-top:30px}
.fcol li{font-size:14.5px;color:var(--white);height:33px;display:flex;gap:14px}
.fcol li::before{content:"»";color:var(--teal)}
.flogo{left:904px;top:3466px;display:flex;align-items:center;gap:10px;color:var(--white);font-weight:700;font-size:18px}
.flogo i{display:block;width:44px;height:44px;border-radius:50%;border:3px solid var(--white)}
.faddr{left:926px;top:3543px;font-size:14.5px;line-height:23px;color:var(--white);display:flex;gap:12px}
.faddr svg{width:12px;height:16px;margin-top:3px}
.contact-bar{position:absolute;left:163px;top:3623px;width:874px;height:57px;background:var(--blue);display:flex;color:var(--white);font-size:16px}
.contact-bar div{display:flex;align-items:center;justify-content:center;gap:20px;height:100%}
.contact-bar .sep{border-right:1px solid rgba(255,255,255,.6);height:38px;margin-top:10px}
.ico{width:40px;height:40px;border:2px solid var(--white);border-radius:50%;display:flex;align-items:center;justify-content:center}
.ico svg{width:20px;height:20px}
.copy{position:absolute;left:0;width:1200px;top:3724px;text-align:center;color:var(--white);font-size:14.5px}
</style>
</head>
<body>
<div class="page">

  <!-- HERO -->
  <div class="hero-photo" role="img" aria-label="Sunset port scene with container ship, cargo plane and a red freight truck"></div>
  <div class="hero-truck" role="img" aria-label="Red semi truck with white trailer"></div>
  <svg class="abs" style="left:0;top:0" width="1200" height="800" viewBox="0 0 1200 800">
    <path d="M0,630 C160,560 330,540 520,590 C720,650 950,720 1200,600 V800 H0Z" fill="#2f6db5"/>
    <path d="M0,685 C170,595 340,575 520,625 C720,685 940,790 1200,655 V800 H0Z" fill="#2bb5a0"/>
    <path d="M0,748 C170,625 360,605 540,665 C740,735 960,795 1200,735 V800 H0Z" fill="#ffffff"/>
  </svg>

  <div class="abs nav-logo"><i></i>Corvane Freight</div>
  <nav class="abs nav">
    <span class="active">Home</span><span>What We Do</span><span>Broker Frieght</span><span>International</span><span>Contact Us</span>
  </nav>
  <div class="pill portal">Customer Portal
    <svg viewBox="0 0 14 14"><circle cx="7" cy="4" r="3.2" fill="#fff"/><path d="M1,14 C1,9 13,9 13,14Z" fill="#fff"/></svg>
  </div>

  <h1 class="abs display hero-title">Freight Broker</h1>
  <p class="abs hero-text">Sed ut perspiciatis unde omnis iste natus error sit voluptatem accusantium doloremque laudantium totam</p>
  <div class="pill teal hero-btn">Let's Get Started
    <svg viewBox="0 0 14 14"><circle cx="7" cy="7" r="7" fill="#fff"/><path d="M4,7 H9 M7,4.5 L9.5,7 L7,9.5" stroke="#2bb5a0" stroke-width="1.8" fill="none"/></svg>
  </div>

  <!-- WHAT WE DO -->
  <h2 class="section-title display" style="top:773px">What We Do</h2>

  <div class="svc" style="left:107px">
    <div class="ph" role="img" aria-label="Cargo plane over container port with trucks at sunset" style="background:linear-gradient(180deg,#7c8fb0 0%,#d98b6a 55%,#5a4a56 100%)"></div>
    <h3>Lorem ipsum dolor sit<br>consectetur</h3>
    <div class="circle-arrow"><svg viewBox="0 0 20 14"><path d="M1,7 H16 M11,2 L17,7 L11,12" stroke="#111" stroke-width="2.6" fill="none"/></svg></div>
  </div>
  <div class="svc" style="left:444px">
    <div class="ph" role="img" aria-label="Warehouse aisle with forklift and stacked pallets" style="background:linear-gradient(180deg,#5b7fb8 0%,#9fb4d6 50%,#e6c59a 100%)"></div>
    <h3>Lorem ipsum dolor sit<br>consectetur</h3>
    <div class="circle-arrow"><svg viewBox="0 0 20 14"><path d="M1,7 H16 M11,2 L17,7 L11,12" stroke="#111" stroke-width="2.6" fill="none"/></svg></div>
  </div>
  <div class="svc" style="left:779px">
    <div class="ph" role="img" aria-label="White truck on a highway at sunrise" style="background:linear-gradient(180deg,#6f8fae 0%,#c9b38a 55%,#4b5540 100%)"></div>
    <h3>Lorem ipsum dolor sit<br>consectetur</h3>
    <div class="circle-arrow"><svg viewBox="0 0 20 14"><path d="M1,7 H16 M11,2 L17,7 L11,12" stroke="#111" stroke-width="2.6" fill="none"/></svg></div>
  </div>

  <div class="pill teal" style="left:501px;top:1264px;width:198px;height:49px">View All Services
    <svg viewBox="0 0 14 14"><circle cx="7" cy="7" r="7" fill="#fff"/><path d="M4,7 H9 M7,4.5 L9.5,7 L7,9.5" stroke="#2bb5a0" stroke-width="1.8" fill="none"/></svg>
  </div>

  <!-- BROKER FREIGHT -->
  <section class="broker" role="img" aria-label="White truck driving on a road at sunset">
    <div class="broker-copy">
      <h2 class="display">Broker Freight</h2>
      <p>Sed ut perspiciatis unde omnis iste natus error sit voluptatem accusantium doloremque laudantium totam rem aperiam, eaque ipsa quae ab illo inventore veritatis et quasi architecto beatae vitae dicta sunt explicabo. Nemo enim ipsam voluptatem quia voluptas sit aspernatur aut odit aut fugit, sed quia consequuntur magni dolores eos qui ratione voluptatem sequi nesciunt. Neque porro quisquam est, qui dolorem ipsum quia dolor sit amet, consectetur, adipisci velit, sed quia non numquam eius</p>
      <div class="pill teal">Learn More
        <svg viewBox="0 0 14 14"><circle cx="7" cy="7" r="7" fill="#fff"/><path d="M4,7 H9 M7,4.5 L9.5,7 L7,9.5" stroke="#2bb5a0" stroke-width="1.8" fill="none"/></svg>
      </div>
    </div>
  </section>

  <!-- WE SPECIALIZED IN -->
  <h2 class="section-title display" style="top:1999px">We Specialized In</h2>

  <div class="spec" style="left:120px">
    <div class="frame" style="background:var(--teal)"></div>
    <div class="ph" role="img" aria-label="Delivery driver in a van handing over a parcel" style="left:9px;background:linear-gradient(135deg,#8c8f95 0%,#c2b7a8 45%,#6d87a6 100%)">
      <span class="label display">Domestic</span>
      <div class="circle-arrow"><svg viewBox="0 0 20 14"><path d="M1,7 H16 M11,2 L17,7 L11,12" stroke="#111" stroke-width="2.6" fill="none"/></svg></div>
    </div>
  </div>
  <div class="spec" style="left:633px">
    <div class="frame" style="background:var(--blue)"></div>
    <div class="ph" role="img" aria-label="Warehouse workers in safety vests checking boxes beside a forklift" style="left:-7px;background:linear-gradient(135deg,#3d3a36 0%,#7a6a55 45%,#b98b4e 75%,#a8a040 100%)">
      <span class="label display">International</span>
      <div class="circle-arrow"><svg viewBox="0 0 20 14"><path d="M1,7 H16 M11,2 L17,7 L11,12" stroke="#111" stroke-width="2.6" fill="none"/></svg></div>
    </div>
  </div>

  <!-- LATEST BLOG -->
  <div class="blog-bg"></div>
  <h2 class="section-title display" style="top:2678px">Latest Blog</h2>

  <article class="post" style="left:105px">
    <div class="ph" role="img" aria-label="Warehouse workers in hard hats checking stock" style="background:linear-gradient(135deg,#5d6f8a 0%,#a88a60 55%,#c9b16a 100%)"></div>
    <div class="date" style="background:var(--blue)"><b>10</b><span>July</span></div>
    <h4>Sed ut perspiciatis unde omnis</h4><hr>
    <p>Ut enim ad minima veniam, quis nostrum exercitationem ullam corporis</p>
    <div class="pill blue">Read More</div>
  </article>
  <article class="post" style="left:442px">
    <div class="ph" role="img" aria-label="Cargo plane above a container port at sunset" style="background:linear-gradient(180deg,#8aa0bd 0%,#e2a070 55%,#6b4a44 100%)"></div>
    <div class="date"><b>10</b><span>July</span></div>
    <h4>Sed ut perspiciatis unde omnis</h4><hr>
    <p>Ut enim ad minima veniam, quis nostrum exercitationem ullam corporis</p>
    <div class="pill teal">Read More</div>
  </article>
  <article class="post" style="left:779px">
    <div class="ph" role="img" aria-label="Forklift in a bright warehouse aisle" style="background:linear-gradient(180deg,#4f74ae 0%,#9db2d4 50%,#e3c49a 100%)"></div>
    <div class="date" style="background:var(--blue)"><b>10</b><span>July</span></div>
    <h4>Sed ut perspiciatis unde omnis</h4><hr>
    <p>Ut enim ad minima veniam, quis nostrum exercitationem ullam corporis</p>
    <div class="pill blue">Read More</div>
  </article>

  <!-- FOOTER -->
  <svg class="footer-bg" viewBox="0 0 1200 623" preserveAspectRatio="none">
    <path d="M0,60 C200,40 420,120 620,160 C860,205 1060,150 1200,30 V623 H0Z" fill="#2bb5a0"/>
    <path d="M0,130 C220,150 420,210 640,235 C880,255 1080,190 1200,95 V623 H0Z" fill="#2f6db5"/>
    <path d="M0,150 C220,175 420,235 650,250 C880,260 1080,205 1200,120 V623 H0Z" fill="#3b3b3b"/>
  </svg>

  <div class="fcol" style="left:114px"><h5>Quick Links</h5><ul><li>Home</li><li>About Us</li><li>Services</li></ul></div>
  <div class="fcol" style="left:382px"><h5>Other Links</h5><ul><li>Terms Of Use</li><li>Privacy Policy</li><li>Contact Us</li></ul></div>
  <div class="fcol" style="left:652px"><h5>Useful Links</h5><ul><li>Sitemap</li><li>Latest Blog</li><li>Help Service</li></ul></div>

  <div class="abs flogo"><i></i>Corvane Freight</div>
  <div class="abs faddr">
    <svg viewBox="0 0 12 16"><path d="M6,0 C2.7,0 0,2.6 0,5.9 C0,10 6,16 6,16 C6,16 12,10 12,5.9 C12,2.6 9.3,0 6,0Z" fill="#2bb5a0"/><circle cx="6" cy="6" r="2.2" fill="#3b3b3b"/></svg>
    <span>4812 Ridgeline Highway<br>Suite 210 United States</span>
  </div>

  <div class="contact-bar">
    <div style="width:259px">
      <span class="ico"><svg viewBox="0 0 20 20"><path d="M5,2 L8,6 L6.5,8 C7.5,10.5 9.5,12.5 12,13.5 L14,12 L18,15 L16,18 C9,18 2,11 2,4Z" fill="none" stroke="#fff" stroke-width="1.6" stroke-linejoin="round"/></svg></span>
      1 800 555 010
    </div>
    <span class="sep"></span>
    <div style="width:283px">
      <span class="ico"><svg viewBox="0 0 20 20"><rect x="3" y="7" width="14" height="10" rx="1" fill="none" stroke="#fff" stroke-width="1.6"/><rect x="6" y="3" width="8" height="5" fill="none" stroke="#fff" stroke-width="1.6"/><path d="M6,11 H14 M6,14 H14" stroke="#fff" stroke-width="1.4"/></svg></span>
      1 800 555 020
    </div>
    <span class="sep"></span>
    <div style="width:330px">
      <span class="ico"><svg viewBox="0 0 20 20"><rect x="2" y="5" width="16" height="11" rx="1" fill="none" stroke="#fff" stroke-width="1.6"/><path d="M2,5 L10,11 L18,5" fill="none" stroke="#fff" stroke-width="1.6"/></svg></span>
      info@corvanefreight.com.au
    </div>
  </div>

  <p class="copy">© 2021 Corvane Freight. All Rights Reserved</p>
</div>
</body>
</html>
```